Business cards for Norwegian software consultancy business

We are in need of business cards for our Norwegian consultancy company.
“Valto Brindex AS” specializes in software development, architecture and agile methodology, providing mostly on-site services at customers.
The cards should reflect a certain level of business professionalism with an elegant touch, while paying tribute to our modern and technological heritage. Our logo should be featured, as well as room for basic information about the cardholder and legal information of the company (company name, address and VAT number).
We would like our cards to reflect that we are a modern consulting company. It should present a professional image that people will remember. The texture and color pallette should reflect our professionalism and reliability, so we prefer a light color pallette with colors such as gray, white, blue and black. The number of colors used should however not be overwhelming, with the text being distinct and readable.
We are open to untraditional layouts and playful designs as long as they communicate the intent stated above.
You could also take a look at our website http://www.brindex.no for input on our visual profile.
Our logo is attached in the form of vectors and rasterized PNG. Please comment if you would like the black-white and/or inverted versions as well.
Industry/Entity Type
Architecture
Contact Information for Business Card
Company information:
Valto Brindex AS
Kvernlia 14, 3170 Sem
482 71 519
info@brindex.no
www.brindex.no
Employee information:
Full name
Title
Email
Phone
Font styles to use
Look and feel

```html
<!DOCTYPE html>
<html lang="en">
<head>
<meta charset="utf-8">
<title>Valto Brindex AS – Business Cards</title>
<link rel="stylesheet" href="https://fonts.googleapis.com/css2?family=Roboto:wght@300;400;700&family=Roboto+Condensed:wght@400;700&display=swap">
<style>
  :root {
    --stage: #5f6a6a;
    --paper: #ffffff;
    --sky: #7fb0d8;
    --sky-deep: #6aa2d0;
    --ink: #000000;
    --ink-soft: #1b1b1b;
    --link-blue: #5a9bd4;
  }
  * { box-sizing: border-box; margin: 0; padding: 0; }
  html, body { width: 1200px; height: 900px; overflow: hidden; }
  body {
    background: var(--stage);
    font-family: "Roboto", Arial, sans-serif;
    position: relative;
  }
  .card {
    position: absolute;
    left: 300px;
    width: 600px;
    height: 340px;
    border-radius: 24px;
    overflow: hidden;
    background: var(--paper);
    display: grid;
    box-shadow: 0 10px 30px rgba(0,0,0,.25);
  }
  .card--contact { top: 70px; grid-template-columns: 62% 38%; }
  .card--brand { top: 490px; grid-template-columns: 38% 62%; }

  /* contact side */
  .contact-panel {
    background: linear-gradient(180deg, var(--sky) 0%, var(--sky-deep) 100%);
    position: relative;
  }
  .brand-lockup {
    position: absolute;
    left: 50%; top: 42%;
    transform: translate(-50%, -50%);
    display: flex; align-items: center; gap: 14px;
  }
  .brand-lockup__mark {
    width: 26px; height: 26px; background: var(--ink-soft);
  }
  .brand-lockup__name {
    font-weight: 300;
    font-size: 32px;
    letter-spacing: 2px;
    color: var(--ink-soft);
    text-transform: uppercase;
    white-space: nowrap;
  }
  .address-band {
    position: absolute; left: 0; right: 0; bottom: 0;
    height: 62px;
    background: var(--ink);
    color: var(--sky);
    font-size: 16px;
    letter-spacing: .5px;
    display: flex; align-items: center; justify-content: center;
  }
  .holder {
    padding: 58px 0 0 22px;
  }
  .holder__name { font-size: 22px; font-weight: 400; color: var(--ink); line-height: 1.1; }
  .holder__title {
    font-family: "Roboto Condensed", Arial, sans-serif;
    font-weight: 700; font-size: 17px; color: var(--ink); margin-bottom: 12px;
  }
  .holder__list { list-style: none; }
  .holder__item {
    display: flex; align-items: center; gap: 10px;
    font-size: 16px; color: var(--link-blue); line-height: 1.45;
  }
  .holder__item svg { width: 15px; height: 15px; flex: none; }

  /* brand side */
  .brand-side {
    display: flex; align-items: center; justify-content: center;
    gap: 12px;
  }
  .brand-side__mark { width: 30px; height: 30px; background: var(--sky-deep); }
  .brand-side__name {
    font-weight: 300; font-size: 26px; letter-spacing: 1px; color: var(--ink-soft);
    text-transform: uppercase; line-height: 1.1;
  }
  .tagline-panel {
    background: linear-gradient(180deg, var(--sky) 0%, var(--sky-deep) 100%);
    position: relative;
  }
  .tagline {
    position: absolute; left: 62px; top: 98px;
    font-family: "Roboto Condensed", Arial, sans-serif;
    font-weight: 700; font-size: 14px; line-height: 1.3;
    color: var(--paper); text-transform: uppercase; letter-spacing: .3px;
  }
  .tagline-band {
    position: absolute; left: 0; right: 0; bottom: 0; height: 62px; background: var(--ink);
  }
</style>
</head>
<body>
  <section class="card card--contact" aria-label="Business card, contact side">
    <div class="contact-panel">
      <div class="brand-lockup">
        <span class="brand-lockup__mark"></span>
        <span class="brand-lockup__name">Valto Brindex</span>
      </div>
      <div class="address-band">Kvernlia 14 / 3170 Sem</div>
    </div>
    <div class="holder">
      <p class="holder__name">Lena Harvik</p>
      <p class="holder__title">Co-Founder &amp; CEO</p>
      <ul class="holder__list">
        <li class="holder__item">
          <svg viewBox="0 0 16 16" aria-hidden="true"><rect x="4" y="1" width="8" height="14" rx="1.5" fill="none" stroke="#1b1b1b" stroke-width="1.4"/><circle cx="8" cy="12.5" r=".9" fill="#1b1b1b"/></svg>
          (007) 555-0182
        </li>
        <li class="holder__item">
          <svg viewBox="0 0 16 16" aria-hidden="true"><rect x="1" y="3" width="14" height="10" fill="none" stroke="#1b1b1b" stroke-width="1.4"/><path d="M1 3l7 6 7-6" fill="none" stroke="#1b1b1b" stroke-width="1.4"/></svg>
          info@brindex.no
        </li>
        <li class="holder__item">
          <svg viewBox="0 0 16 16" aria-hidden="true"><circle cx="8" cy="8" r="6.5" fill="none" stroke="#1b1b1b" stroke-width="1.3"/><ellipse cx="8" cy="8" rx="3" ry="6.5" fill="none" stroke="#1b1b1b" stroke-width="1.1"/><path d="M1.5 8h13" stroke="#1b1b1b" stroke-width="1.1"/></svg>
          brindex.no
        </li>
      </ul>
    </div>
  </section>

  <section class="card card--brand" aria-label="Business card, brand side">
    <div class="brand-side">
      <span class="brand-side__mark"></span>
      <span class="brand-side__name">Valto<br>Brindex</span>
    </div>
    <div class="tagline-panel">
      <p class="tagline">Rental of qualified resources<br>in software development,<br>project management and IT operations</p>
      <div class="tagline-band"></div>
    </div>
  </section>
</body>
</html>
```